Storm Restoration Contractor needs a professional letterhead design

Looking for a professional letterhead design. Not looking for your cheapo MS Word standard ones that are readily available. Dont want it to be cookie cutter look like ones readily available online. We just recently changed our logo and want to freshen up all our documents. Our company handles restoring a property back to a pre-loss condition after a storm damages it. For example, wind, hail, flood, fire losses.

Target Market(s)

Property Owners, Homeowners, Property Owners, Commercial Property Owners, Property Management Companies

Industry/Entity Type

Construction Company

Requirements
Must have
• Professional, Use 1 of 2 logo options
• Storm Restoration, Roofing, Siding, Windows

```html
<!DOCTYPE html>
<html lang="en">
<head>
<meta charset="utf-8">
<title>Stormline Restoration Letterhead</title>
<link href="https://fonts.googleapis.com/css2?family=Open+Sans:wght@400;600;700&display=swap" rel="stylesheet">
<style>
  :root {
    --brand-blue: #1e73be;
    --band-gray: #4a4a4f;
    --ink: #555a60;
    --ink-dark: #2b2e33;
    --paper: #ffffff;
    --backdrop: #e9e9eb;
  }
  * { margin: 0; padding: 0; box-sizing: border-box; }
  html, body {
    width: 1200px; height: 795px; overflow: hidden;
    background: var(--backdrop);
    font-family: "Open Sans", Arial, sans-serif;
  }
  .letterhead {
    position: absolute; left: 322px; top: 16px;
    width: 556px; height: 763px;
    background: var(--paper);
    box-shadow: 0 2px 10px rgba(0,0,0,0.12);
  }
  .brand {
    position: absolute; left: 48px; top: 46px;
    display: flex; align-items: center; gap: 10px;
  }
  .brand-dot {
    width: 34px; height: 34px; border-radius: 50%;
    background: var(--brand-blue);
  }
  .brand-name {
    font-size: 15px; font-weight: 700; letter-spacing: 1.5px;
    color: var(--brand-blue); text-transform: uppercase;
  }
  .website {
    position: absolute; right: 48px; top: 56px;
    font-size: 10px; color: var(--brand-blue);
  }
  .letter-body {
    position: absolute; left: 48px; top: 150px; width: 440px;
    font-size: 9.5px; line-height: 1.55; color: var(--ink);
  }
  .salutation {
    font-size: 11px; font-weight: 700; color: var(--ink-dark);
    margin-bottom: 14px;
  }
  .letter-body p { margin-bottom: 14px; }
  .signature {
    width: 110px; height: 38px; margin-top: 20px;
    background: linear-gradient(90deg, rgba(40,40,45,0.15), rgba(40,40,45,0.05));
    border-radius: 4px;
  }
  .footer-rule {
    position: absolute; left: 0; right: 0; bottom: 92px; height: 6px;
    background: var(--band-gray);
  }
  .footer-band {
    position: absolute; left: 0; right: 0; bottom: 0; height: 92px;
    background: var(--brand-blue); color: #fff;
    padding: 0 40px; display: flex; align-items: center; justify-content: space-between;
  }
  .contact { font-size: 10.5px; line-height: 1.7; }
  .contact b { font-weight: 700; margin-right: 3px; }
  .contact .sep { margin-left: 8px; }
  .footer-brand {
    display: flex; align-items: center; gap: 8px;
    font-size: 11px; font-weight: 700; letter-spacing: 1px; text-transform: uppercase;
  }
  .footer-dot { width: 26px; height: 26px; border-radius: 50%; background: #fff; }
</style>
</head>
<body>
  <div class="letterhead">
    <div class="brand">
      <div class="brand-dot"></div>
      <span class="brand-name">Stormline Restoration</span>
    </div>
    <div class="website">www.stormlinerestoration.com</div>

    <div class="letter-body">
      <div class="salutation">Dear Mr. Harlan,</div>
      <p>Lorem Ipsum is simply dummy text of the printing and typesetting industry. Lorem Ipsum has been the industry's standard dummy text ever since the 1500s, when an unknown printer took a galley of type and scrambled it to make a type specimen book. It has survived not only five centuries, but also the leap into electronic typesetting, remaining essentially unchanged.</p>
      <p>The standard chunk of Lorem Ipsum used since the 1500s is reproduced below for those interested. Sections 1.10.32 and 1.10.33 from "de Finibus Bonorum et Malorum" by Cicero are also reproduced in their exact original form, accompanied by English versions from the 1914 translation by H. Rackham.</p>
      <p>Lorem Ipsum is simply dummy text of the printing and typesetting industry. Lorem Ipsum has been the industry's standard dummy text ever since the 1500s, when an unknown printer took a galley of type and scrambled it to make a type specimen book. It has survived not only five centuries, but also the leap into electronic typesetting, remaining essentially unchanged. It was popularised in the</p>
      <div class="signature" role="img" aria-label="Handwritten signature"></div>
    </div>

    <div class="footer-rule"></div>
    <div class="footer-band">
      <div class="contact">
        <div>480 Meridian Loop, Fairfield, CA 94534</div>
        <div><b>P :</b>(555) 214-7380<span class="sep"><b>F :</b>(555) 214-7381</span><span class="sep"><b>E :</b>info@stormlinerestoration.com</span></div>
      </div>
      <div class="footer-brand">
        <div class="footer-dot"></div>
        <span>Stormline</span>
      </div>
    </div>
  </div>
</body>
</html>
```